The Polish & Glow Studio Website Update

Hello. I am seeking to freshen up my website with a clean and easy feel that incorporates our modern chic style. Our services cater to mostly young professionals and modern moms.

We focus on natural nail care and gentle professional waxing. We are known for our cleanliness. Our clients like our current website, however I'm hoping to make it look even more professional and user friendly. Some clients have even said our current website feels welcoming, unlike other websites that in they feel give a snobbish vibe. I like clean lines, simple, fresh, and sometimes bold. Totally NOT a fan of whimsical.

I threw added an accent color to the color pallet...however it should be used in moderation. I am also open to other accent colors. I'd like the site to emphasize the Brazilian wax as much as nails, if not more than nail. The photos downloaded are just to give you a few images of who we are, however are not necessary. Current website www.thepolishandglowstudio.example

Target Market(s)

Females 30-55

Industry/Entity Type

Beauty Salon

Coding

Coded - Design and coding required

Number of Pages Required

5+ page

Font styles to use
Sans Serif

Colors
ffffff
1b1b1b
acd136
eeeeee
878787
c4c4c4
efefef
7f7f7f

Requirements
Must have
• Clean look
Nice to have
• Our logo
Should not have
• Whimsical

```html
<!DOCTYPE html>
<html lang="en">
<head>
<meta charset="utf-8">
<title>The Polish &amp; Glow Studio</title>
<link rel="stylesheet" href="https://fonts.googleapis.com/css2?family=Raleway:wght@400;500&family=Open+Sans:wght@400;600&family=Marcellus&display=swap">
<style>
:root{
  --white:#ffffff;
  --ink:#1b1b1b;
  --green:#acd136;
  --light:#eeeeee;
  --grey:#878787;
  --silver:#c4c4c4;
  --mist:#efefef;
  --nav:#7f7f7f;
  --navdark:#5e5e5e;
  --text:#666666;
}
*{margin:0;padding:0;box-sizing:border-box}
html,body{width:674px;height:1200px;overflow:hidden;background:var(--white)}
body{position:relative;font-family:"Open Sans",sans-serif;color:var(--text)}
.abs{position:absolute}

/* header */
.brand{left:48px;top:20px;font-family:"Raleway",sans-serif;font-weight:400;font-size:21px;color:#6d6d6d;line-height:24px;display:flex;align-items:center;gap:7px}
.brand-dot{width:10px;height:10px;border-radius:50%;background:var(--green)}
.schedule-btn{left:516px;top:30px;width:110px;height:24px;border:2px solid var(--green);color:var(--green);font-size:10.5px;display:flex;align-items:center;justify-content:center;gap:5px}
.nav{left:0;top:65px;width:674px;height:30px;background:var(--nav);display:flex;padding-left:46px}
.nav a{color:var(--white);text-decoration:none;font-size:10.5px;line-height:30px;padding:0 8px;border-right:1px solid #999}
.nav a:last-child{border-right:none}
.nav a.active{background:var(--navdark);padding:0 13px}

/* hero */
.hero{left:0;top:95px;width:674px;height:260px;background:linear-gradient(160deg,#e8e2dc 0%,#d8b9a4 45%,#c79a82 70%,#e4ddd6 100%)}
.hero-title{left:0;top:163px;width:674px;text-align:center;font-family:"Raleway",sans-serif;color:var(--white);font-size:29px;font-weight:500}
.hero-sub{left:0;top:195px;width:674px;text-align:center;font-family:"Raleway",sans-serif;color:var(--white);font-size:22px}
.dots{left:314px;top:305px;display:flex;gap:3px}
.dots span{width:9px;height:9px;border-radius:50%;background:var(--white)}
.dots span.on{background:var(--green);border:1.5px solid var(--white)}

/* feature cards */
.card{top:323px;width:187px;height:204px;background:var(--white);border:1px solid #dcdcdc;text-align:center}
.card-head{height:32px;background:var(--green);color:var(--white);font-family:"Raleway",sans-serif;font-size:13.5px;line-height:32px;margin:-1px -1px 0}
.card-img{height:98px}
.card p{font-size:8px;line-height:13px;color:#9a9a9a;padding:9px 6px 0}
.card-btn{display:inline-block;margin-top:8px;border:1.5px solid var(--ink);color:var(--ink);font-size:7.5px;font-weight:600;padding:5px 10px}

/* about */
.about-band{left:0;top:558px;width:674px;height:222px;background:linear-gradient(90deg,#ececec,#f3f3f3 60%,#e6e6e6)}
.about-title{left:62px;top:592px;font-family:"Raleway",sans-serif;font-weight:400;font-size:20px;color:#3b3b3b}
.about-copy{left:61px;top:631px;width:320px;font-size:7.8px;line-height:12.4px;color:#6b6b6b}
.about-copy p+p{margin-top:6px}
.ring{left:400px;top:572px;width:196px;height:196px;border-radius:50%;border:1px solid #bdbdbd;background:var(--white)}
.ring-img{left:407px;top:579px;width:182px;height:182px;border-radius:50%;background:linear-gradient(160deg,#cfcfcf 0%,#bdbdb8 45%,#6e8a5e 70%,#4b4b4b 100%)}

/* services */
.menu-title{left:0;top:797px;width:674px;text-align:center;font-family:"Marcellus",serif;font-size:20px;color:var(--green)}
.menu-line{top:812px;height:1px;background:linear-gradient(90deg,transparent,var(--silver))}
.service{top:835px;width:112px;text-align:center;color:var(--ink)}
.svc-ring{width:84px;height:84px;margin:0 auto;border-radius:50%;border:2px solid var(--green);padding:4px}
.svc-img{width:100%;height:100%;border-radius:50%}
.service h3{font-size:9.5px;font-weight:400;margin-top:10px;color:#222}
.service small{display:block;font-size:7px;color:#9a9a9a;margin-top:2px}
.service b{display:block;font-weight:400;font-size:13px;margin-top:2px;color:#333}

/* footer */
.wave{left:0;top:990px}
.footer{left:0;top:1030px;width:674px;height:134px;background:#000}
.foot-brand{left:52px;top:1052px;width:132px;font-family:"Raleway",sans-serif;font-size:16px;line-height:20px;color:#d8d8d8}
.foot-col{top:1043px;color:#cfcfcf;font-size:8.2px}
.foot-col h4{font-family:"Raleway",sans-serif;font-weight:400;font-size:11.5px;color:var(--white);margin-bottom:8px}
.foot-col li{list-style:none;line-height:17.4px}
.bottom-bar{left:0;top:1164px;width:674px;height:36px;background:#2b2b2b;color:#9a9a9a;font-size:7.5px;line-height:36px;padding-left:48px}
</style>
</head>
<body>

<header>
  <div class="abs brand"><span class="brand-dot"></span>The Polish &amp; Glow Studio</div>
  <a class="abs schedule-btn">
    <svg width="11" height="11" viewBox="0 0 12 12" fill="none" stroke="#acd136" stroke-width="1.2"><rect x="1" y="2" width="10" height="9"/><path d="M1 5h10M4 1v2M8 1v2M4 7h1M7 7h1M4 9h1M7 9h1"/></svg>
    Schedule online!
  </a>
  <nav class="abs nav">
    <a class="active">Home</a><a>Schedule An Appointment</a><a>Products and Services</a><a>Careers</a><a>Specials</a><a>About Us</a><a>FAQ</a><a>Contact Us</a>
  </nav>
</header>

<section>
  <div class="abs hero" role="img" aria-label="Close-up photo of hands with a French manicure"></div>
  <h1 class="abs hero-title">The Most Meticulous Manicures,</h1>
  <div class="abs hero-sub">Pedicures &amp; Waxing service</div>
  <div class="abs dots"><span class="on"></span><span></span><span></span><span></span></div>
</section>

<section>
  <div class="abs card" style="left:48px">
    <div class="card-head">Why Choose Us</div>
    <div class="card-img" role="img" aria-label="Photo of the salon interior with manicure stations" style="background:linear-gradient(180deg,#cfd3d6,#7a7d80 60%,#3e3e40)"></div>
    <p>Suspendisse quam leo molestie sed luctus quis feugiat in pede Fusce tellus Sed metus</p>
    <span class="card-btn">READ MORE</span>
  </div>
  <div class="abs card" style="left:243px">
    <div class="card-head">Schedule an Appointment</div>
    <div class="card-img" role="img" aria-label="Photo of folded hands with painted nails" style="background:linear-gradient(160deg,#e7d7cc,#c9a592 55%,#8c6c5e)"></div>
    <p>Suspendisse quam leo molestie sed luctus quis feugiat in pede Fusce tellus Sed metus</p>
    <span class="card-btn">CLICK HERE</span>
  </div>
  <div class="abs card" style="left:439px">
    <div class="card-head">Special Offers</div>
    <div class="card-img" role="img" aria-label="Photo of a relaxed client in a swimsuit" style="background:linear-gradient(150deg,#7fd3ef,#3bb7e0 45%,#e6c2a8 75%,#f2f2f2)"></div>
    <p>Suspendisse quam leo molestie sed luctus quis feugiat in pede Fusce tellus Sed metus</p>
    <span class="card-btn">READ MORE</span>
  </div>
</section>

<section>
  <div class="abs about-band"></div>
  <h2 class="abs about-title">The Polish &amp; Glow Studio</h2>
  <div class="abs about-copy">
    <p>To be the #1 nail and wax salon in the Maple Ridge, VT area, offering the most meticulous manicures, pedicures, and waxing service. We use superior products, advanced techniques, and exceptional sanitation procedures to provide our clients with safe, quality services.</p>
    <p>Our knowledgeable and friendly staff is always happy to assist with any of your Nail &amp; Wax concerns. We are excited to welcome another Licensed Nail Technician to our team, Dana Whitfield. Dana has over 25 years experience and is also a certified Medical Nail Technician</p>
  </div>
  <div class="abs ring"></div>
  <div class="abs ring-img" role="img" aria-label="Photo of a clean waxing treatment room"></div>
</section>

<section>
  <div class="abs menu-line" style="left:76px;width:188px"></div>
  <div class="abs menu-line" style="left:408px;width:198px;transform:scaleX(-1)"></div>
  <h2 class="abs menu-title">Service Menu</h2>

  <div class="abs service" style="left:59px">
    <div class="svc-ring"><div class="svc-img" role="img" aria-label="Manicure photo" style="background:linear-gradient(150deg,#f3d6da,#d99aa7)"></div></div>
    <h3>Signature Manicure</h3><small>Mauris vel lacus vita</small><b>$24</b>
  </div>
  <div class="abs service" style="left:172px">
    <div class="svc-ring"><div class="svc-img" role="img" aria-label="Gel manicure photo" style="background:linear-gradient(150deg,#f1e0d4,#d8a17f)"></div></div>
    <h3>Gel Polish Manicure</h3><small>Mauris vel lacus vita</small><b>$34</b>
  </div>
  <div class="abs service" style="left:283px">
    <div class="svc-ring"><div class="svc-img" role="img" aria-label="Pedicure photo" style="background:linear-gradient(150deg,#e8c7b5,#7a3f5e)"></div></div>
    <h3>Signature Pedicure</h3><small>Mauris vel lacus vita</small><b>$40</b>
  </div>
  <div class="abs service" style="left:395px">
    <div class="svc-ring"><div class="svc-img" role="img" aria-label="Brow waxing photo" style="background:linear-gradient(150deg,#e9b64a,#f0dccd)"></div></div>
    <h3>Brow Design</h3><small>Mauris vel lacus vita</small><b>$13</b>
  </div>
  <div class="abs service" style="left:507px">
    <div class="svc-ring"><div class="svc-img" role="img" aria-label="Body waxing photo" style="background:linear-gradient(150deg,#f3ede8,#d9b7a1)"></div></div>
    <h3>Brazilian</h3><small>Mauris vel lacus vita</small><b>$55</b>
  </div>
</section>

<footer>
  <svg class="abs wave" width="674" height="42" viewBox="0 0 674 42">
    <path d="M0 32 Q200 -6 420 6 T674 2 L674 42 L0 42Z" fill="#c4c4c4"/>
    <path d="M0 36 Q200 2 420 12 T674 8 L674 42 L0 42Z" fill="#000"/>
  </svg>
  <div class="abs footer"></div>
  <div class="abs foot-brand">The Polish &amp;<br>Glow Studio</div>
  <div class="abs foot-col" style="left:199px"><h4>Quick Links</h4><ul><li>Home</li><li>Products</li><li>Our Services</li></ul></div>
  <div class="abs foot-col" style="left:302px"><h4>Resources</h4><ul><li>Careers</li><li>Specials</li><li>About Us</li><li>FAQ</li></ul></div>
  <div class="abs foot-col" style="left:399px"><h4>Support</h4><ul><li>Contact Us</li><li>Privacy Policy</li><li>Book an Appointment</li></ul></div>
  <div class="abs foot-col" style="left:514px"><h4>Contact Info</h4><ul><li>412 Orchard Lane Suite</li><li>Maple Ridge, VT 05001</li><li>Phone: (555) 014-2737</li><li>Email: hello@polishandglow.example</li></ul></div>
  <div class="abs bottom-bar">© 2016 Company Name &nbsp;All right reserved &nbsp;Term of Use</div>
</footer>

</body>
</html>
```